Fizz's Shed & Grill Burger Restaurant Website - HomePage Only PSD

I need a website design for a restaurant called "Fizz's Shed and Grill" featuring burgers, wings, beer, live music, trivia, and more. I have several images of the restaurant and they already have their logo files created (see attached). I want some type of wood background and integrate the silver tin. This needs to be a modern, hip and fun type design. Design must incorporate these attached graphics.

UPDATE - just added a few more images of things I really like to be incorporated into my designs.
Updates

Industry/Entity Type

Burger Restaurant

Number of Pages Required

1 page

Font styles to use
Sans Serif

Requirements
Must have
• Restaurant/Bar theme with integration of existing logo and the red wood look.
Nice to have
• - Modern Fun appearance
• - Use Pelko Fonts

```html
<!DOCTYPE html>
<html lang="en">
<head>
<meta charset="utf-8">
<title>Fizz's Shed & Grill</title>
<link href="https://fonts.googleapis.com/css2?family=Architects+Daughter&family=Open+Sans:wght@400;600;700&display=swap" rel="stylesheet">
<style>
:root{
  --red:#d5262b;
  --green:#7aad1e;
  --ink:#2b2b2b;
  --muted:#9a9a9a;
  --navy:#262a36;
  --silver-a:#d9d9d9;
  --silver-b:#b6b6b6;
  --paper:#e4e4e4;
  --white:#ffffff;
}
*{box-sizing:border-box;margin:0;padding:0}
html,body{width:1200px;height:3285px;overflow:hidden}
body{font-family:'Open Sans',sans-serif;color:var(--ink);background:var(--white);position:relative}
.hand{font-family:'Architects Daughter',cursive}
section,header,footer{position:absolute;left:0;width:1200px}

/* header */
.site-header{top:0;height:153px;background:var(--white);border-bottom:3px solid var(--green)}
.nav-link{position:absolute;top:66px;font-family:'Architects Daughter',cursive;font-size:15px;color:#444;transform:translateX(-50%)}
.nav-link.active{top:40px;width:76px;height:76px;border:2px solid var(--green);border-radius:50%;display:flex;align-items:center;justify-content:center;color:var(--green)}
.nav-link.active::before{content:"";position:absolute;inset:5px;border:1px solid var(--green);border-radius:50%}
.brand{position:absolute;left:600px;transform:translateX(-50%);display:flex;align-items:center;gap:10px;font-family:'Architects Daughter',cursive;color:var(--ink);line-height:1.1;text-align:center}
.brand .dot{width:16px;height:16px;border:2px solid var(--ink);border-radius:50%}
.header-brand{top:48px;font-size:22px}

/* hero */
.hero{top:153px;height:552px;background:linear-gradient(110deg,#5d7896 0%,#8a6b4e 35%,#b08a66 55%,#7c6350 80%,#cfc9c1 100%)}
.hero-copy{position:absolute;left:653px;top:258px;color:var(--white);font-family:'Architects Daughter',cursive}
.hero-copy .kicker{font-size:26px}
.hero-copy h1{font-weight:400;font-size:44px;color:var(--red);line-height:1.1}
.hero-copy .sub{font-size:22px}
.slider-arrows{position:absolute;left:576px;top:498px;display:flex;gap:4px}
.slider-arrows span{width:22px;height:22px;background:rgba(255,255,255,.85);display:flex;align-items:center;justify-content:center;font-size:12px;color:#555}

/* features */
.features{top:705px;height:412px;background:linear-gradient(180deg,var(--silver-b),var(--silver-a) 40%,#c4c4c4 100%)}
.feature-divider{position:absolute;top:15px;bottom:15px;border-left:2px dashed rgba(255,255,255,.6)}
.feature{position:absolute;top:76px;width:300px;text-align:center;transform:translateX(-50%)}
.feature-ring{width:154px;height:154px;margin:0 auto;border-radius:50%;background:var(--white);border:3px solid #8c8c8c;display:flex;align-items:center;justify-content:center}
.feature-ring .inner{width:130px;height:130px;border-radius:50%;border:2px solid var(--red);display:flex;align-items:center;justify-content:center}
.feature h3{font-family:'Architects Daughter',cursive;font-weight:400;font-size:30px;color:var(--red);margin-top:32px;line-height:1}
.feature p{font-family:'Architects Daughter',cursive;font-size:15px;color:#666;margin-top:4px}
.feature a{display:block;margin-top:12px;font-family:'Architects Daughter',cursive;font-size:14px;color:var(--white);text-decoration:none}
.side-arrow{position:absolute;top:186px;font-size:40px;color:rgba(255,255,255,.8);font-family:'Open Sans',sans-serif}

/* about */
.about{top:1117px;height:547px;background:radial-gradient(ellipse at 60% 50%,#d7d2c6 0%,#a79a82 45%,#5a5446 100%)}
.about-photo{position:absolute;left:120px;top:70px;width:625px;height:412px;border:5px solid var(--white);background:linear-gradient(180deg,#3b8ad8 0%,#6ab0ea 45%,#8a3a22 46%,#a64a2a 100%)}
.about-card{position:absolute;left:628px;top:83px;width:517px;height:359px;background:#2c2c2c;border:6px solid #3a3a3a;color:#bdbdbd;text-align:center;padding:34px 50px}
.card-brand{position:static;transform:none;justify-content:center;color:var(--white);font-size:22px}
.card-brand .dot{border-color:var(--white)}
.about-card p{font-size:12.5px;line-height:1.75;margin-top:44px}
.about-card a{display:inline-block;margin-top:22px;font-size:12.5px;color:var(--white);text-decoration:none;font-weight:600}

/* menu */
.menu{top:1664px;height:916px;background:var(--paper)}
.menu h2{position:absolute;top:52px;width:100%;text-align:center;font-family:'Architects Daughter',cursive;font-weight:400;font-size:34px;color:#222}
.menu .lead{position:absolute;top:114px;width:100%;text-align:center;font-size:13px;color:#333}
.menu .note{position:absolute;top:140px;width:100%;text-align:center;font-size:13px;color:#e88a2e}
.dish{position:absolute;width:243px}
.dish-photo{height:193px}
.dish h4{font-size:13px;font-weight:600;color:#222;margin-top:24px;line-height:1.35}
.dish p{font-size:11.5px;color:var(--muted);margin-top:4px;line-height:1.55;padding-bottom:10px;border-bottom:1px dashed #b5b5b5}

/* banner */
.banner{top:2580px;height:322px;background:linear-gradient(90deg,#2a2622,#4a3d33 40%,#6a5646 60%,#2f2a26)}
.banner-copy{position:absolute;top:90px;width:100%;text-align:center;color:var(--white);font-family:'Architects Daughter',cursive;font-size:44px;line-height:1.25}

/* footer */
.site-footer{top:2902px;height:230px;background:#dcdcdc}
.foot-title{position:absolute;top:38px;font-family:'Architects Daughter',cursive;font-size:18px;color:#333}
.foot-title span{color:var(--green)}
.foot-links{position:absolute;top:92px;list-style:none;font-size:12px;color:#444;line-height:30.5px}
.foot-links li::before{content:"›";margin-right:10px;color:#888}
.news-input{position:absolute;left:457px;top:96px;width:296px;height:36px;background:var(--white);font-size:11px;color:#999;padding:11px 12px}
.news-btn{position:absolute;left:457px;top:138px;width:296px;height:36px;background:var(--green);color:var(--white);font-size:12px;font-weight:600;text-align:center;line-height:36px}
.social{position:absolute;top:97px;left:862px;display:flex;gap:21px}
.social span{width:34px;height:34px;border-radius:50%;border:2px solid var(--green)}

/* bottom bar */
.bottom-bar{top:3132px;height:153px;background:var(--navy);color:var(--white)}
.hours{position:absolute;left:88px;top:34px;font-size:12px;line-height:26px}
.hours li{list-style:none;display:flex}
.hours .day{width:60px}
.hours .dash{width:86px;border-bottom:1px dashed #8a8e99;margin:0 8px 9px 0}
.bottom-brand{top:56px;color:var(--white);font-size:20px}
.bottom-brand .dot{border-color:var(--white)}
.legal{position:absolute;right:88px;top:36px;text-align:right;font-size:12px;line-height:26px}
.legal .name{font-family:'Architects Daughter',cursive;color:var(--green);font-size:16px}
.legal .red{color:var(--red)}
</style>
</head>
<body>

<header class="site-header">
  <a class="nav-link active" style="left:147px">Home</a>
  <a class="nav-link" style="left:285px">About</a>
  <a class="nav-link" style="left:431px">Foods</a>
  <div class="brand header-brand"><span class="dot"></span><span>Fizz's Shed<br>and Grill</span></div>
  <a class="nav-link" style="left:782px">News</a>
  <a class="nav-link" style="left:920px">Store</a>
  <a class="nav-link" style="left:1069px">Contact</a>
</header>

<section class="hero" role="img" aria-label="Photo of a smiling couple dining at the restaurant">
  <div class="hero-copy">
    <div class="kicker">We are</div>
    <h1>Fizz's Shed &amp; Grill</h1>
    <div class="sub">based in united states of america</div>
  </div>
  <div class="slider-arrows"><span>‹</span><span>›</span></div>
</section>

<section class="features">
  <div class="feature-divider" style="left:394px"></div>
  <div class="feature-divider" style="left:817px"></div>
  <span class="side-arrow" style="left:18px">‹</span>
  <span class="side-arrow" style="left:1160px">›</span>

  <div class="feature" style="left:190px">
    <div class="feature-ring"><div class="inner">
      <svg width="70" height="70" viewBox="0 0 70 70"><circle cx="35" cy="35" r="33" fill="var(--red)"/><path d="M20 32a15 11 0 0 1 30 0z" fill="#fff"/><rect x="19" y="35" width="32" height="4" rx="2" fill="#fff"/><path d="M20 42h30v3a4 4 0 0 1-4 4H24a4 4 0 0 1-4-4z" fill="#fff"/></svg>
    </div></div>
    <h3>Burgers</h3><p>Lorem ipsum dolor sit amet</p><a>View Now</a>
  </div>

  <div class="feature" style="left:607px">
    <div class="feature-ring"><div class="inner">
      <svg width="70" height="70" viewBox="0 0 70 70"><circle cx="35" cy="35" r="33" fill="var(--red)"/><circle cx="35" cy="35" r="22" fill="none" stroke="#fff" stroke-width="2"/><circle cx="35" cy="35" r="8" fill="#fff"/><circle cx="35" cy="35" r="3" fill="var(--red)"/></svg>
    </div></div>
    <h3>Live Music</h3><p>Lorem ipsum dolor sit amet</p><a>View Now</a>
  </div>

  <div class="feature" style="left:1012px">
    <div class="feature-ring"><div class="inner">
      <svg width="70" height="70" viewBox="0 0 70 70"><circle cx="35" cy="35" r="33" fill="var(--red)"/><rect x="22" y="22" width="20" height="28" rx="2" fill="#fff"/><path d="M42 28h5a4 4 0 0 1 4 4v8a4 4 0 0 1-4 4h-5" fill="none" stroke="#fff" stroke-width="3"/><rect x="20" y="17" width="24" height="7" rx="3.5" fill="#fff"/></svg>
    </div></div>
    <h3>Beer</h3><p>Lorem ipsum dolor sit amet</p><a>View Now</a>
  </div>
</section>

<section class="about" role="img" aria-label="Blurred photo of a plated salad">
  <div class="about-photo" role="img" aria-label="Photo of the restaurant's red wood gable with its sign against a blue sky"></div>
  <div class="about-card">
    <div class="brand card-brand"><span class="dot"></span><span>Fizz's Shed<br>and Grill</span></div>
    <p>Lorem ipsum dolor sit amet, consectetur adipiscing elit. Duis vitae gravida nulla. Integer fermentum dui non commodo venenatis. Vestibulum gravida dui in imperdiet tristique. Ligula libero tincidunt enim, et finibus eros massa eu elit. Etiam venenatis tortor at purus convallis volutpat.</p>
    <a>Read More &gt;&gt;</a>
  </div>
</section>

<section class="menu">
  <h2>All Day Menu</h2>
  <div class="lead">Our meat is free range &amp; organic where possible. Breads are sourdough, baked daily</div>
  <div class="note">See front counter for daily sweet selection</div>

  <article class="dish" style="left:79px;top:212px"><div class="dish-photo" role="img" aria-label="Photo of crostino pie" style="background:linear-gradient(160deg,#8a6a4a,#efe9e0 60%,#3a2a20)"></div><h4>Crostino Pie</h4><p>with Cove Dairy butter &amp; spreads</p></article>
  <article class="dish" style="left:344px;top:212px"><div class="dish-photo" role="img" aria-label="Photo of a burger with fries" style="background:linear-gradient(160deg,#6a4a30,#c8883a 50%,#5a3a22)"></div><h4>Pollo Burger</h4><p>with Earl Grey figs, seasonal fruit &amp; yogurt</p></article>
  <article class="dish" style="left:609px;top:212px"><div class="dish-photo" role="img" aria-label="Photo of eggplant special pie on a table" style="background:linear-gradient(160deg,#5a4030,#d8c8b0 55%,#7a5a40)"></div><h4>Eggplant Special Pie</h4><p>with poached red fruits</p></article>
  <article class="dish" style="left:874px;top:212px"><div class="dish-photo" role="img" aria-label="Photo of a taco pizza" style="background:linear-gradient(160deg,#b8412a,#e0a050 50%,#8a3020)"></div><h4>Taco Pizza</h4><p>with Earl Grey figs, seasonal fruit &amp; yogurt</p></article>

  <article class="dish" style="left:79px;top:543px"><div class="dish-photo" role="img" aria-label="Photo of smoked salmon plate" style="background:linear-gradient(160deg,#7a9a40,#b85a2a 50%,#6a2a1a)"></div><h4>Smoked Riverbend salmon plate</h4><p>with toast with house made sauce, pickled fennel and roe</p></article>
  <article class="dish" style="left:344px;top:543px"><div class="dish-photo" role="img" aria-label="Photo of a grilled steak sandwich" style="background:linear-gradient(160deg,#e8e4dc,#d8a060 50%,#5a8a3a)"></div><h4>Ridgeline Station wagyu steak sandwich</h4><p>with red onion jam, radicchio, tomato, house pickles &amp; aioli</p></article>
  <article class="dish" style="left:609px;top:543px"><div class="dish-photo" role="img" aria-label="Photo of breakfast dishes" style="background:linear-gradient(160deg,#3a2a20,#c07a3a 50%,#2a2018)"></div><h4>Buffalo's Big Breakfast</h4><p>Pesto, sausage, bacon, fried eggs, roast tomato, field mushrooms</p></article>
  <article class="dish" style="left:874px;top:543px"><div class="dish-photo" role="img" aria-label="Photo of poached eggs with bottles" style="background:linear-gradient(160deg,#3a2a1a,#9a5a2a 50%,#b8302a)"></div><h4>Two poached eggs on sourdough</h4><p>with smoked tomato relish, field mushroom, avocado, feta</p></article>
</section>

<section class="banner" role="img" aria-label="Dim photo of guests dining together">
  <div class="banner-copy">Fizz's Shed and Grill<br>Lorem dummy text food</div>
</section>

<footer class="site-footer">
  <div class="foot-title" style="left:88px">Category <span>List</span></div>
  <ul class="foot-links" style="left:88px"><li>Home</li><li>About</li><li>Culture</li></ul>
  <ul class="foot-links" style="left:236px"><li>News</li><li>Work</li><li>Contact</li></ul>

  <div class="foot-title" style="left:455px">News<span>letter</span></div>
  <div class="news-input">Enter Your Email Address</div>
  <div class="news-btn">Subscribe</div>

  <div class="foot-title" style="left:854px">Follow <span>Us</span></div>
  <div class="social"><span></span><span></span><span></span><span></span><span></span></div>
</footer>

<footer class="bottom-bar">
  <ul class="hours">
    <li><span class="day">Monday</span><span class="dash"></span>Friday 8.00 - 22.00</li>
    <li><span class="day">Saturday</span><span class="dash"></span>Sunday 7.30 - 22.30</li>
    <li><span class="day">Holidays</span><span class="dash"></span>7.00 - 24.00</li>
  </ul>
  <div class="brand bottom-brand"><span class="dot"></span><span>Fizz's Shed<br>and Grill</span></div>
  <div class="legal">
    <div class="name">Fizz's Shed and Grill</div>
    <div>© 2016 All Rights Reserved</div>
    <div><span class="red">Terms of use</span> and <span class="red">Privacy Policy</span></div>
  </div>
</footer>

</body>
</html>
```